Harbor Wonder Hour - A magic website for a monthly modern magic show

Looking to build a website to promote my new monthly magic show

Sites like this. https://velvetloftshow.example/ https://sevencuriouscardsnight.example/

Target Market(s)

18-65 year old men and women who enjoy live entertainment especially magic

Industry/Entity Type

Entertainment

Coding

Coded - Design and coding required

Number of Pages Required

3 page

Colors

Designer to choose colors to be used in the design.

Requirements
Must have
• Wanting a wordpress site.
• Contact form, media section for photos and videos to be posted.
• A “reviews/testimonials” section.

```html
<!DOCTYPE html>
<html lang="en">
<head>
<meta charset="utf-8">
<title>Harbor Wonder Hour — Contact</title>
<link rel="stylesheet" href="https://fonts.googleapis.com/css2?family=Poppins:wght@400;500;600;700;800&display=swap">
<style>
  :root {
    --bg-dark: #1c1c1e;
    --bg-mid: #2e2e31;
    --panel: #232323;
    --text: #ffffff;
    --text-soft: #e6e6e6;
    --accent: #e07a2e;
    --line: #6a6a6a;
    --dot-dim: #9a5a2a;
  }
  * { box-sizing: border-box; margin: 0; padding: 0; }
  html, body { width: 1200px; height: 800px; overflow: hidden; }
  body {
    position: relative;
    font-family: "Poppins", sans-serif;
    color: var(--text);
    background: var(--bg-dark);
  }
  .hero-backdrop {
    position: absolute; inset: 0;
    background:
      radial-gradient(ellipse at 40% 20%, #3a3a3e 0%, transparent 45%),
      radial-gradient(ellipse at 70% 75%, #2b2b2f 0%, transparent 55%),
      linear-gradient(180deg, var(--bg-mid) 0%, var(--bg-dark) 100%);
  }
  .site-header {
    position: absolute; top: 40px; left: 44px; right: 43px;
    display: flex; justify-content: space-between; align-items: center;
  }
  .brand { font-size: 17px; font-weight: 800; letter-spacing: 0.2px; }
  .main-nav { display: flex; gap: 24px; }
  .main-nav a {
    color: var(--text); text-decoration: none;
    font-size: 11px; font-weight: 600; letter-spacing: 0.1px;
  }
  .panel {
    position: absolute; top: 193px; width: 504px; height: 415px;
    background: var(--panel);
    text-align: center;
  }
  .testimonials { left: 74px; }
  .contact { left: 622px; }
  .panel-title { font-size: 24px; font-weight: 700; letter-spacing: 0.2px; }
  .testimonials .panel-title { margin-top: 94px; }
  .reviewer {
    margin-top: 42px;
    color: var(--accent); font-size: 13px; font-weight: 600;
  }
  .review {
    margin: 14px auto 0; width: 420px;
    font-size: 11.5px; line-height: 22px; color: var(--text-soft);
  }
  .slider-dots { display: flex; justify-content: center; gap: 8px; margin-top: 24px; }
  .slider-dots span { width: 7px; height: 7px; border-radius: 50%; background: var(--dot-dim); }
  .slider-dots span.active { background: var(--accent); }
  .contact .panel-title { margin-top: 38px; }
  .contact-form { margin: 24px 44px 0 45px; text-align: left; }
  .field {
    display: block; width: 100%;
    margin-top: 22px;
    background: none; border: none; border-bottom: 1px solid var(--line);
    font-family: "Poppins", sans-serif; font-size: 10px; font-weight: 500;
    color: var(--text); padding: 8px 0 5px; outline: none;
  }
  .field:first-child { margin-top: 12px; }
  .field::placeholder { color: var(--text); }
  .send-btn {
    display: block; margin: 44px auto 0;
    width: 163px; height: 37px;
    background: var(--accent); color: var(--text);
    border: none; font-family: "Poppins", sans-serif;
    font-size: 10px; font-weight: 700; letter-spacing: 0.5px;
  }
  .social-links {
    position: absolute; left: 44px; top: 629px;
    list-style: none; display: flex; flex-direction: column; gap: 22px;
  }
  .social-links a {
    color: var(--text); text-decoration: none;
    font-size: 10px; font-weight: 600;
  }
  .social-links a.highlight { color: var(--accent); }
  .scroll-cue {
    position: absolute; left: 1144px; top: 676px;
    writing-mode: vertical-rl;
    font-size: 10px; font-weight: 600; letter-spacing: 0.6px;
  }
</style>
</head>
<body>
  <div class="hero-backdrop" role="img" aria-label="Dark moody photo of a wet street with a reflection of a figure in a puddle"></div>

  <header class="site-header">
    <div class="brand">NAME</div>
    <nav class="main-nav">
      <a href="#tricks">TRICKS</a>
      <a href="#contact">CONTACT ME</a>
    </nav>
  </header>

  <section class="panel testimonials">
    <h2 class="panel-title">WHAT THEY SAY</h2>
    <p class="reviewer">MARCUS DELANEY</p>
    <p class="review">The Velvet Loft, in collaboration with Cardhouse Co, presents THE MAGICIAN, an intimate evening of magic, mystery, and deception. Starring Theo Grant. Every Weekend.</p>
    <div class="slider-dots"><span></span><span class="active"></span><span></span></div>
  </section>

  <section class="panel contact" id="contact">
    <h2 class="panel-title">CONTACT ME</h2>
    <form class="contact-form">
      <input class="field" type="text" placeholder="YOUR NAME...">
      <input class="field" type="email" placeholder="YOUR EMAIL...">
      <input class="field" type="text" placeholder="YOUR SUBJECT...">
      <input class="field" type="text" placeholder="YOUR MESSAGE...">
      <button class="send-btn" type="button">SEND MESSAGE NOW</button>
    </form>
  </section>

  <ul class="social-links">
    <li><a href="#">Circlo</a></li>
    <li><a href="#" class="highlight">Echo</a></li>
    <li><a href="#">Linqo</a></li>
    <li><a href="#">Folio</a></li>
  </ul>

  <div class="scroll-cue">SCROLL DOWN</div>
</body>
</html>
```